Super elegant, crisp & clean Business card design required

We recently upgraded our branding - which is on our website - talvendoraphoto.com

I would like a simple, yet elegant, clean business card design please.

The font of my logo is Cinzel - and because of the natural colour - it's best to have this on a black background.

I would like to have the back of the business card - with simply my logo.

PLEASE DO NOT SUBMIT A COMPLICATED / UNCLEAN DESIGN

Industry/Entity Type

Business

Contact Information for Business Card

Talven Doroshko Photography

Font styles to use
Other font styles liked:
• Cinzel

Requirements
Must have
• A backpage with nothing but my logo
• Simple design - stands out
Should not have
• Colour that dont align with my logo
• Over complicated '/ non symmetrical design

```html
<!DOCTYPE html>
<html lang="en">
<head>
<meta charset="utf-8">
<title>Talven Doroshko Photography – Business Card</title>
<link href="https://fonts.googleapis.com/css2?family=Cinzel:wght@400&family=Open+Sans:wght@400;600&display=swap" rel="stylesheet">
<style>
  :root {
    --stage: #e9e6e1;
    --card-black: #050505;
    --card-charcoal: #2a2a2a;
    --taupe: #8a7a66;
    --taupe-light: #9c8c78;
    --white: #ffffff;
    --shadow: rgba(0, 0, 0, 0.28);
  }
  * { margin: 0; padding: 0; box-sizing: border-box; }
  html, body {
    width: 1200px; height: 900px; overflow: hidden;
    background: var(--stage);
  }
  .stage { position: relative; width: 1200px; height: 900px; }

  .card {
    position: absolute;
    width: 600px; height: 343px;
    overflow: hidden;
    box-shadow: 0 12px 30px var(--shadow);
  }

  /* Back of card: logo only */
  .card-back {
    left: 520px; top: 70px;
    background: var(--card-charcoal);
    display: flex; align-items: center; justify-content: center;
  }
  .brand-name {
    font-family: "Cinzel", serif;
    font-weight: 400;
    text-align: center;
    line-height: 1.25;
  }
  .card-back .brand-name { color: var(--white); font-size: 30px; letter-spacing: 1px; }
  .brand-name .tagline { display: block; letter-spacing: 9px; }

  /* Front of card */
  .card-front {
    left: 80px; top: 480px;
    background: var(--card-black);
    font-family: "Open Sans", sans-serif;
    color: var(--white);
  }
  .corner-mark { position: absolute; left: 0; top: 14px; }
  .person { position: absolute; left: 52px; top: 12px; }
  .person-name { color: var(--taupe-light); font-size: 21px; font-weight: 400; line-height: 1.1; }
  .person-role { font-size: 13px; font-weight: 600; margin-top: 2px; }

  .contact { position: absolute; left: 34px; top: 110px; list-style: none; font-size: 14px; line-height: 21px; }
  .contact .address { padding-left: 24px; margin-bottom: 2px; }
  .contact li { display: flex; align-items: center; }
  .contact svg { width: 14px; height: 14px; margin-right: 10px; fill: var(--taupe-light); flex: none; }

  .card-front .brand-name {
    position: absolute; right: 40px; top: 140px; width: 290px;
    color: var(--taupe); font-size: 24px; letter-spacing: 1px;
  }
  .footer-band { position: absolute; left: 0; bottom: 0; }
</style>
</head>
<body>
<main class="stage">

  <section class="card card-back" aria-label="Business card back">
    <div class="brand-name">Talven Doroshko<span class="tagline">Photography</span></div>
  </section>

  <section class="card card-front" aria-label="Business card front">
    <svg class="corner-mark" width="46" height="32" viewBox="0 0 46 32" aria-hidden="true">
      <polygon points="0,0 46,0 24,32 0,32" fill="var(--taupe)"/>
      <polygon points="30,0 46,0 46,32 8,32" fill="var(--card-black)" opacity="0"/>
    </svg>

    <div class="person">
      <div class="person-name">Elias Marrow</div>
      <div class="person-role">Managing Director</div>
    </div>

    <ul class="contact">
      <li class="address">12345, Address Goes Here<br>Country Name, 123456</li>
      <li>
        <svg viewBox="0 0 24 24" aria-hidden="true"><path d="M6.6 10.8a15.1 15.1 0 0 0 6.6 6.6l2.2-2.2c.3-.3.7-.4 1-.2 1.1.4 2.3.6 3.6.6.6 0 1 .4 1 1V20c0 .6-.4 1-1 1A17 17 0 0 1 3 4c0-.6.4-1 1-1h3.5c.6 0 1 .4 1 1 0 1.3.2 2.5.6 3.6.1.3 0 .7-.2 1z"/></svg>
        (044)-456-7890
      </li>
      <li>
        <svg viewBox="0 0 24 24" aria-hidden="true"><path d="M6 2h9l3 3v4H6zM3 10h18v8h-3v4H6v-4H3zm5 5v5h8v-5z"/></svg>
        123-456-7890
      </li>
      <li>
        <svg viewBox="0 0 24 24" aria-hidden="true"><path d="M2 5h20v14H2zm2 2v.5l8 5.5 8-5.5V7z"/></svg>
        info@youremail.com
      </li>
      <li>
        <svg viewBox="0 0 24 24" aria-hidden="true"><path d="M12 2a10 10 0 1 0 0 20 10 10 0 0 0 0-20zm0 2c1.2 0 2.5 2.2 2.9 6H9.1C9.5 6.2 10.8 4 12 4zm-7.9 8h3c.1 2.5.6 4.6 1.4 6A8 8 0 0 1 4.1 12zm0-2a8 8 0 0 1 4.4-6c-.8 1.4-1.3 3.5-1.4 6zm5 2h5.8c-.4 3.8-1.7 6-2.9 6s-2.5-2.2-2.9-6zm7.8 0h3a8 8 0 0 1-4.4 6c.8-1.4 1.3-3.5 1.4-6zm0-2c-.1-2.5-.6-4.6-1.4-6a8 8 0 0 1 4.4 6z"/></svg>
        www.talvendoraphoto.com
      </li>
    </ul>

    <div class="brand-name">Talven Doroshko<span class="tagline">Photography</span></div>

    <svg class="footer-band" width="600" height="70" viewBox="0 0 600 70" aria-hidden="true">
      <rect x="0" y="30" width="600" height="40" fill="var(--taupe)"/>
      <polygon points="0,18 290,18 270,50 0,50" fill="var(--card-black)"/>
      <polygon points="0,2 8,2 8,16 0,16" fill="var(--taupe)"/>
      <polygon points="272,18 290,18 270,50 252,50" fill="var(--white)"/>
    </svg>
  </section>

</main>
</body>
</html>
```